Lotstallmart.com Webpage Design

Design Brief for lotstallmart.com (Copy of Brief also in attached Word file)

Name of Website- lotstallmart.com (existing logo and look & feel of website to be changed)

Logo - Finalised. The logo files are attached with the brief as “logo.jpeg”. The “Blue- Grey” version of the logo is for use on lighter backgrounds and the “Orange-White” version of the logo is for use on darker backgrounds. (A full Black version of the logo is also attached). Both versions may be used in different parts of the website. All attached files are in .png format.
Status - The website in functional and is undergoing user trials. However, we want to improve the look & feel of the website so at it seems
a. cotemporary,
b. Easy to Navigate
c. professional and
d. Vibrant.

Please visit ‘lotstallmart.com’ to check out the website and its functionalities – please use it only as a reference for the features & functions to be provided, however the designer should use a ‘Free Hand’ in designing the composition of various parts of the webpage without getting too influenced by the existing design

Objective of the Website ‘lotstallmart.com –
a. It is a portal focussed on listing of ‘Retail’ specific real-estate properties by developers, owners and realty brokers. The properties shall listed under the following four categories-
i. Retail Malls
ii. Shopping Complexes
iii. High-street shops
iv. Retail Warehouses
*refer lotstallmart.com for better clarity

b. The abovementioned properties shall be listed either for ‘Sale’ or ‘rent\lease’ or both

c. Users shall visit the site in case they wish to acquire a retail \ shop space either on ‘sale’ or ‘rent’. These Users would be able to specify the ‘Search Criteria’ through the tool-bars provided on the website – the ‘Search Criteria’ shall comprise of ‘Type of space category’, ‘City’, ‘Locality’, transaction type ie ‘Rent \ Sale’ and ‘Area Range’

d. The main revenue model for the website shall be listing fee ( or advertising charges ) payable by those listing their properties on the website.

Three Main Pages of Website (lotstallmart.com) that need to be designed -
a. Main Home Page (visit the web link - http://lotstallmart.com/ ) - The main home page has the “Search Toolbar” for specifying of Search Criteria by the User. It shall also have the following features & functions-
i. Main Advertising Banner
ii. Featured Projects
iii. New Launches
iv. Toolbar with buttons – ‘Advertise with Us’, ‘Listings Alert’, ‘Mart Wizards’, ‘Advertiser Login’

b. Property Listings Page (visit the web link - http://lotstallmart.com/gurgaon-in-india ) - The List of property options that match the Criteria specified by the ‘User’ get displayed on this page.

c. Property Detail Page - When the ‘User’ clicks on the “More….” Button on the ‘Property Listings Page’ (given in point b. above) the web page with the details of the property opens. (For Example – visit the web link - http://lotstallmart.com/vorne-Shopping-Complex-vorne-quadrion-gurgaon-636 )

Note:- Please refer to attached ‘Shopping’ related images the designer may use them on the website to provide a look & feel of retail if required – either separately or rotate in a single window

Target Market(s)

Retailers & Investors looking for retail space, Real Estate Brokers, Developers

Industry/Entity Type

Advertising

Number of Pages Required

3 page

Requirements
Must have
• Refer to existing site lotstallmart.com -- all the existing functionalities are a must have.
Nice to have
• The Designer may use the retail related images on the website if required for making it more vibrant. Refer attached images Shopping(1-6).jpg

```html
<!DOCTYPE html>
<html lang="en">
<head>
<meta charset="utf-8">
<title>Lotstallmart.com</title>
<link href="https://fonts.googleapis.com/css2?family=Open+Sans:wght@400;600;700&display=swap" rel="stylesheet">
<style>
:root{
  --bg:#1e1e1f;
  --band:#252526;
  --card:#2a2a2b;
  --footer:#1a1a1a;
  --bottom:#151515;
  --orange:#f2a51c;
  --orange-dark:#d88c0a;
  --text:#9a9a9a;
  --muted:#7a7a7a;
  --light:#e8e8e8;
  --line:#3a3a3a;
}
*{box-sizing:border-box;margin:0;padding:0}
html,body{width:1200px;height:2532px;overflow:hidden;background:var(--bg)}
body{font-family:"Open Sans",Arial,sans-serif;color:var(--text);position:relative}
.page{position:relative;width:1200px;height:2532px;overflow:hidden;border-top:4px solid var(--orange)}
.topbar{position:absolute;top:4px;left:0;width:1200px;height:48px;border-bottom:1px solid var(--line);font-size:11.5px}
.topbar .email{position:absolute;left:100px;top:16px;display:flex;align-items:center;gap:8px;white-space:nowrap}
.cities{position:absolute;right:100px;top:0;display:flex;height:48px;white-space:nowrap}
.cities span{padding:16px 8px 0;border-left:1px solid var(--line);font-size:11.5px}
.brandrow{position:absolute;top:76px;left:100px;width:1000px;height:60px}
.logo{display:flex;align-items:center;gap:10px;font-size:30px;font-weight:700;color:var(--light);position:absolute;top:6px;line-height:1.1}
.logo .dot{width:30px;height:30px;border-radius:50%;background:var(--orange)}
.logo small{display:block;font-size:8px;color:var(--orange);font-weight:600;letter-spacing:.5px}
.adv-btn{position:absolute;right:0;top:3px;width:167px;height:38px;border:1px solid #444;background:#1a1a1a;color:#aaa;font-size:13px;display:flex;align-items:center;justify-content:center}
.nav{position:absolute;top:155px;left:100px;width:1000px;height:57px;background:var(--orange);display:flex;align-items:center;border-radius:3px 3px 0 0}
.nav a{color:#fff;font-weight:600;font-size:13px;padding:0 20px;height:57px;display:flex;align-items:center;border-right:1px solid rgba(0,0,0,.12);text-decoration:none;white-space:nowrap}
.nav .search{margin-left:auto;margin-right:15px;width:218px;height:36px;background:#fff;border-radius:3px;display:flex;align-items:center;gap:10px;padding-left:12px;font-size:11px;color:#999}
.hero{position:absolute;top:212px;left:100px;width:1000px;height:561px;border:3px solid #fff;background:linear-gradient(120deg,#6f5f4a 0%,#b8a78c 35%,#e07a1e 55%,#c9b89a 75%,#6b5b46 100%)}
.hero .arrows{position:absolute;right:25px;bottom:22px;width:46px;height:22px;background:#555;display:flex;justify-content:space-around;align-items:center;color:#ddd;font-size:13px}
.finder{position:absolute;top:388px;left:150px;width:333px;height:446px;background:#fff;border-radius:4px;box-shadow:0 4px 12px rgba(0,0,0,.4);padding:0 22px}
.ribbon{position:absolute;top:-25px;left:50%;transform:translateX(-50%);width:190px;height:62px;background:var(--orange);border-radius:0 0 40px 40px;color:#fff;font-weight:700;font-size:14px;text-align:center;line-height:20px;padding-top:10px}
.formats{display:grid;grid-template-columns:1fr 1fr;gap:12px 10px;margin-top:60px;font-size:11px;color:#666}
.formats span{display:flex;align-items:center;gap:8px;white-space:nowrap}
.formats i{width:12px;height:13px;border:1px solid #999;background:#eee;display:inline-block}
.finder label{display:block;font-size:11px;color:#666;margin:18px 0 6px}
.select{height:29px;border:1px solid #ddd;background:#f5f5f5;font-size:11px;color:#666;padding:7px 10px;position:relative}
.select.dd:after{content:"";position:absolute;right:14px;top:12px;border:5px solid transparent;border-top-color:#777}
.go{display:block;margin:22px auto 0;width:156px;height:39px;background:#2a2a2a;color:#fff;font-weight:700;font-size:17px;border:0;letter-spacing:1px;font-family:inherit}
.welcome{position:absolute;top:868px;left:0;width:1200px;text-align:center}
.welcome h1{font-weight:400;font-size:25px;color:var(--orange)}
.welcome p{font-size:13px;color:#555;margin-top:12px}
.cats{position:absolute;top:979px;left:100px;width:1000px;display:flex}
.cat{width:250px;text-align:center}
.cat .ic{width:84px;height:84px;border:2px solid #333;border-radius:50%;margin:0 auto;display:flex;align-items:center;justify-content:center}
.cat h3{font-size:14px;font-weight:600;color:#aaa;margin-top:20px;letter-spacing:.5px}
.cat p{font-size:11px;color:#777;margin:10px auto 0;width:210px;line-height:19px}
.section{position:absolute;left:0;width:1200px}
.section.alt{background:var(--band)}
.section h2{position:absolute;left:100px;font-size:16px;color:var(--orange);font-weight:700}
.section .pager{position:absolute;right:100px;width:36px;height:17px;display:flex;gap:2px}
.section .pager i{flex:1;background:#555;color:#ccc;font-size:10px;font-style:normal;text-align:center;line-height:17px}
.cards{position:absolute;left:100px;display:flex;gap:18px}
.card{width:236px;height:338px;background:var(--card);padding:8px;text-align:center}
.card .pic{height:155px;position:relative}
.card .pic span{position:absolute;left:0;bottom:0;background:rgba(0,0,0,.65);color:#fff;font-size:12px;font-weight:700;padding:3px 14px}
.card h4{color:var(--orange);font-size:14px;font-weight:700;margin-top:19px}
.card p{font-size:11px;color:#777;line-height:18px;margin:9px 8px 0}
.card .btn{display:inline-block;margin-top:15px;width:123px;height:35px;background:var(--orange);border-bottom:3px solid var(--orange-dark);color:#fff;font-size:11px;font-weight:700;line-height:33px;border-radius:2px}
.brands{position:absolute;top:2107px;left:100px;width:1000px;height:96px;border-top:1px solid #333;border-bottom:1px solid #333;display:flex;justify-content:space-around;align-items:center}
.brands span{font-family:"Open Sans",Arial,sans-serif;font-size:28px;font-weight:700;color:#3b3b3b}
.footer{position:absolute;top:2248px;left:0;width:1200px;height:228px;background:var(--footer)}
.fcol{position:absolute;top:22px}
.fcol h5{color:var(--orange);font-size:14px;font-weight:700}
.fcol p{font-size:10px;color:#ccc;line-height:19px;margin-top:14px}
.contact li{list-style:none;font-size:10px;color:#ccc;display:flex;align-items:center;gap:12px;margin-top:6px}
.field{width:241px;height:37px;border:1px solid #444;background:#151515;font-size:11px;color:#ddd;padding:11px 14px;margin-top:14px}
.sub{margin-top:14px;width:102px;height:36px;background:var(--orange);border-bottom:3px solid var(--orange-dark);color:#fff;font-size:12px;font-weight:600;text-align:center;line-height:33px}
.bottombar{position:absolute;top:2476px;left:0;width:1200px;height:56px;background:var(--bottom);border-bottom:5px solid var(--orange)}
.bottombar p{position:absolute;left:100px;top:20px;font-size:10px;color:#aaa}
.social{position:absolute;right:100px;top:10px;display:flex;gap:10px}
.social i{width:30px;height:30px;border:2px solid #777;border-radius:50%;display:block}
</style>
</head>
<body>
<div class="page">
  <div class="topbar">
    <div class="email">
      <svg width="14" height="10" viewBox="0 0 14 10"><rect x=".5" y=".5" width="13" height="9" fill="none" stroke="#999"/><path d="M.5 .5 7 6l6.5-5.5" fill="none" stroke="#999"/></svg>
      Email : support@lotstallmart.com
    </div>
    <div class="cities">
      <span>Bangalore</span><span>Chennai</span><span>Greater Noida</span><span>Gurgaon | Hyderabad</span><span>Jaipur</span><span>Khanna</span><span>Kolkatta</span><span>Mumbai</span><span>Noida</span><span>Pune</span><span>Surat</span>
    </div>
  </div>

  <div class="brandrow">
    <div class="logo"><span class="dot"></span><div>lotstallmart<small>INDIA'S LEADING PORTAL FOR RETAIL SPACE</small></div></div>
    <div class="adv-btn">ADVERTISER LOGIN</div>
  </div>

  <nav class="nav">
    <a>HOME</a><a>ADVERTISE WITH US</a><a>LISTINGS ALERT</a><a>MART WIZARDS</a><a>ADVERTISER LOGIN</a>
    <div class="search"><svg width="12" height="12" viewBox="0 0 12 12"><circle cx="5" cy="5" r="3.6" fill="none" stroke="#333" stroke-width="1.8"/><path d="M7.6 7.6 11 11" stroke="#333" stroke-width="2"/></svg>Enter any keyword ....</div>
  </nav>

  <div class="hero" role="img" aria-label="Banner photo of a smiling shopper in orange holding shopping bags inside a mall">
    <div class="arrows"><span>‹</span><span>›</span></div>
  </div>

  <div class="finder">
    <div class="ribbon">SELECT RETAIL<br>FORMAT</div>
    <div class="formats">
      <span><i></i>RETAIL MALLS</span><span><i></i>SHOPPING COMPLEX</span>
      <span><i></i>HIGH STREET SHOPS</span><span><i></i>RETAIL WAREHOUSES</span>
    </div>
    <label>Sale Or Rent Or Both:</label><div class="select dd">Both</div>
    <label>Select City:</label><div class="select dd">Select</div>
    <label>Select Locality/Micro-Market:</label><div class="select dd">Select</div>
    <label>Enter Keywords:</label><div class="select">Name</div>
    <button class="go">SEARCH</button>
  </div>

  <div class="welcome">
    <h1>WELCOME TO LOTSTALLMART</h1>
    <p>CONTRARY TO POPULAR BELIEF, LOREM IPSUM IS NOT SIMPLY RANDOM TEXT. IT HAS ROOTS IN A PIECE OF CLASSICAL LATIN LITERATURE</p>
  </div>

  <div class="cats">
    <div class="cat"><div class="ic"><svg width="36" height="36" viewBox="0 0 36 36" fill="#444"><rect x="6" y="8" width="24" height="26"/><g fill="#1e1e1f"><rect x="10" y="12" width="4" height="4"/><rect x="16" y="12" width="4" height="4"/><rect x="22" y="12" width="4" height="4"/><rect x="10" y="19" width="4" height="4"/><rect x="16" y="19" width="4" height="4"/><rect x="22" y="19" width="4" height="4"/><rect x="15" y="26" width="6" height="8"/></g></svg></div><h3>RETAIL MALLS</h3><p>Contrary to popular belief, Lorem Ipsum is not simply random text.</p></div>
    <div class="cat"><div class="ic"><svg width="38" height="36" viewBox="0 0 38 36" fill="none" stroke="#444" stroke-width="3"><path d="M2 6h6l5 18h18l4-13H10"/><circle cx="15" cy="30" r="2.5" fill="#444"/><circle cx="28" cy="30" r="2.5" fill="#444"/></svg></div><h3>SHOPPING COMPLEX</h3><p>Contrary to popular belief, Lorem Ipsum is not simply random text.</p></div>
    <div class="cat"><div class="ic"><svg width="34" height="36" viewBox="0 0 34 36" fill="#444"><path d="M13 4h8l7 26H6z"/><rect x="2" y="30" width="30" height="4"/><rect x="9" y="14" width="16" height="4" fill="#1e1e1f"/></svg></div><h3>HIGH STREET SHOPS</h3><p>Contrary to popular belief, Lorem Ipsum is not simply random text.</p></div>
    <div class="cat"><div class="ic"><svg width="30" height="40" viewBox="0 0 30 40"><text x="15" y="32" text-anchor="middle" font-family="Open Sans,Arial,sans-serif" font-size="34" font-weight="700" fill="#444">$</text></svg></div><h3>RETAIL WAREHOUSES</h3><p>Contrary to popular belief, Lorem Ipsum is not simply random text.</p></div>
  </div>

  <section class="section" style="top:1200px;height:420px">
    <h2 style="top:4px">FEATURED RETAIL PROJECTS</h2>
    <div class="pager" style="top:6px"><i>‹</i><i>›</i></div>
    <div class="cards" style="top:49px">
      <div class="card"><div class="pic" role="img" aria-label="Photo of a modern retail building" style="background:linear-gradient(180deg,#9fb9d2,#b8a686 55%,#6d7566)"><span>SURAT</span></div><h4>CORVEL ARCADE</h4><p>Contrary to popular belief, Lorem Ipsum is not simply random text. It has roots in a piece of classical Latin literature</p><div class="btn">VIEW THE LISTING</div></div>
      <div class="card"><div class="pic" role="img" aria-label="Photo of a mall lit up at dusk with palm trees" style="background:linear-gradient(180deg,#2f3340,#8d6a42 55%,#2a2620)"><span>FARIDABAD</span></div><h4>CORVEL ARCADE</h4><p>Contrary to popular belief, Lorem Ipsum is not simply random text. It has roots in a piece of classical Latin literature</p><div class="btn">VIEW THE LISTING</div></div>
      <div class="card"><div class="pic" role="img" aria-label="Photo of an open-air shopping plaza with umbrellas" style="background:linear-gradient(180deg,#d8dde2,#a9aeb2 50%,#5e6367)"><span>GURGAON</span></div><h4>CORVEL ARCADE</h4><p>Contrary to popular belief, Lorem Ipsum is not simply random text. It has roots in a piece of classical Latin literature</p><div class="btn">VIEW THE LISTING</div></div>
      <div class="card"><div class="pic" role="img" aria-label="Photo of a mall facade with large screens" style="background:linear-gradient(180deg,#3c4a66,#6e5a6a 50%,#36363c)"><span>NEW DELHI</span></div><h4>CORVEL ARCADE</h4><p>Contrary to popular belief, Lorem Ipsum is not simply random text. It has roots in a piece of classical Latin literature</p><div class="btn">VIEW THE LISTING</div></div>
    </div>
  </section>

  <section class="section alt" style="top:1629px;height:422px">
    <h2 style="top:20px">FEATURED NEW LAUNCHES</h2>
    <div class="pager" style="top:22px"><i>‹</i><i>›</i></div>
    <div class="cards" style="top:68px">
      <div class="card"><div class="pic" role="img" aria-label="Rendering of a circular mall entrance" style="background:linear-gradient(180deg,#5c6a7e,#a7a7a5 55%,#4a4d52)"><span>SURAT</span></div><h4>CORVEL ARCADE</h4><p>Contrary to popular belief, Lorem Ipsum is not simply random text. It has roots in a piece of classical Latin literature</p><div class="btn">VIEW THE LISTING</div></div>
      <div class="card"><div class="pic" role="img" aria-label="Rendering of a glass tower with retail podium" style="background:linear-gradient(180deg,#1f3450,#4f6f94 55%,#2a2a34)"><span>FARIDABAD</span></div><h4>CORVEL ARCADE</h4><p>Contrary to popular belief, Lorem Ipsum is not simply random text. It has roots in a piece of classical Latin literature</p><div class="btn">VIEW THE LISTING</div></div>
      <div class="card"><div class="pic" role="img" aria-label="Rendering of a curved commercial building at night" style="background:linear-gradient(180deg,#14243d,#3b5a86 50%,#1c1e26)"><span>GURGAON</span></div><h4>CORVEL ARCADE</h4><p>Contrary to popular belief, Lorem Ipsum is not simply random text. It has roots in a piece of classical Latin literature</p><div class="btn">VIEW THE LISTING</div></div>
      <div class="card"><div class="pic" role="img" aria-label="Rendering of a shopping centre lit at night" style="background:linear-gradient(180deg,#2a3350,#7a6440 55%,#262018)"><span>NEW DELHI</span></div><h4>CORVEL ARCADE</h4><p>Contrary to popular belief, Lorem Ipsum is not simply random text. It has roots in a piece of classical Latin literature</p><div class="btn">VIEW THE LISTING</div></div>
    </div>
  </section>

  <div class="brands">
    <span>TARNWELL</span><span>veluna</span><span>Orrin</span><span>lumeo</span><span>Kestrad</span><span>Halvik</span>
  </div>

  <footer class="footer">
    <div class="fcol" style="left:106px;width:330px">
      <h5>EDITOR'S CHOICE</h5>
      <p>A "Select" Listing of Retail Properties Handpicked by our Editors based on their own positive evaluation on parameters &amp; attributes such as Design Concept, Location, Developer, Success Potential. So Read On to Check Out for yourself</p>
      <p style="margin-top:12px">Nemo enim ipsam voluptatem quia voluptas sit aspernatur aut odit aut fugit, sed quia consequuntur magni nescient A "Select" Listing of Retail tion, So Read On to Check Out for yourself</p>
    </div>
    <div class="fcol" style="left:505px;width:270px">
      <h5>CONTACT US</h5>
      <p>Fusce dapibus, tellus condimentum utellus fermalsuada magna. Fusce dapibus, tellus magna.</p>
      <ul class="contact" style="margin-top:10px">
        <li><svg width="8" height="11" viewBox="0 0 8 11"><path d="M4 0a4 4 0 0 1 4 4c0 3-4 7-4 7S0 7 0 4a4 4 0 0 1 4-4z" fill="#f2a51c"/><circle cx="4" cy="4" r="1.4" fill="#1a1a1a"/></svg>585 E lorem ipsum dummy</li>
        <li style="padding-left:20px;margin-top:2px">CT 06051</li>
        <li><svg width="10" height="10" viewBox="0 0 10 10"><path d="M1 3c0-2 8-2 8 0v1H7V3H3v1H1zM2 5h6l1 4H1z" fill="#f2a51c"/></svg>(000)-121-1231</li>
        <li><svg width="10" height="8" viewBox="0 0 10 8"><rect width="10" height="8" rx="1" fill="#f2a51c"/><path d="M0 0l5 4 5-4" fill="none" stroke="#1a1a1a"/></svg>info@lotstallmart.com</li>
      </ul>
    </div>
    <div class="fcol" style="left:839px;width:260px">
      <h5>LISTING ALERT</h5>
      <div class="field">Enter Your Name :</div>
      <div class="field">Enter Your Password :</div>
      <div class="sub">SUBSCRIBE</div>
    </div>
  </footer>

  <div class="bottombar">
    <p>© Copy Rights 2014 Lotstallmart.com All Rights Reserved</p>
    <div class="social" aria-label="Social links"><i></i><i></i><i></i><i></i><i></i></div>
  </div>
</div>
</body>
</html>
```